Design a Website for an IT Support Company

We are an IT support company that provides commercial IT support and services to small and medium sized businesses. We are in need of a website to be developed for our business.
We would like to work with someone who is either familiar with the IT field, or has developed a website for an IT support company in the past.
Some examples of designs/layouts that we like:
https://www.veldaworks.example/
http://www.marsbyquill.example/
http://817kq.example/
http://www.olbenstructures.example/
http://www.bykq.example/
I have attached a word document that gives a menu system/page layout format that we would like for our website as well as branch office phone numbers. Our logo is also attached that you can use for your design purposes. We currently do not have copy produced for all of the pages outlined in the word document, but would get this done during the project with the selected designer.
We would like the website to be SEO friendly & fully responsive. We would prefer a Wordpress format, however, we are open to HTML formats as well.

```html
<!DOCTYPE html>
<html lang="en">
<head>
<meta charset="utf-8">
<title>Kestrel IT – Commercial IT Support</title>
<link href="https://fonts.googleapis.com/css2?family=Montserrat:wght@400;500&family=Roboto:wght@300;400;500&display=swap" rel="stylesheet">
<style>
:root{
  --blue:#1a73b8;
  --blue-dark:#13619e;
  --blue-band-a:#1976bd;
  --blue-band-b:#4f7fa6;
  --ink:#222;
  --grey:#777;
  --line:#dcdcdc;
  --hero-a:#eef5fb;
  --hero-b:#c9dff0;
  --white:#fff;
}
*{margin:0;padding:0;box-sizing:border-box}
html,body{width:772px;height:1200px;overflow:hidden;background:var(--white)}
body{position:relative;font-family:"Roboto",Arial,sans-serif;color:var(--ink)}
.abs{position:absolute}
.top-rule{left:0;top:0;width:772px;height:2px;background:#ddd}
.brand{left:64px;top:24px;display:flex;align-items:center;gap:6px;font-family:"Montserrat",sans-serif;font-weight:500;font-size:17px;color:var(--blue)}
.brand .dot{width:14px;height:14px;border-radius:50%;background:var(--blue)}
.call{right:68px;top:11px;font-size:14px;display:flex;align-items:center;gap:6px}
.call b{font-weight:400;color:var(--blue)}
.nav{right:70px;top:40px;display:flex;align-items:center;gap:21px;font-size:8.5px}
.nav .active{color:var(--blue)}
.nav .search{width:20px;height:20px;border-radius:50%;background:var(--blue);display:flex;align-items:center;justify-content:center}
.header-rule{left:0;top:66px;width:772px;height:1px;background:#e4e4e4}
.hero{left:0;top:67px;width:772px;height:283px;background:linear-gradient(120deg,var(--hero-a),var(--hero-b) 55%,#e7f0f8)}
.hero-photo{left:420px;top:67px;width:352px;height:283px;background:linear-gradient(90deg,rgba(215,228,240,0),#8e9fb2 30%,#4f5e70 70%,#c8d5e2)}
.hero-text{left:100px;top:174px;width:308px;text-align:center;font-family:"Montserrat",sans-serif;font-size:13px;line-height:16px}
.btn{display:flex;align-items:center;justify-content:center;background:var(--blue-dark);color:var(--white);border-radius:14px;font-size:9.5px;font-weight:500}
.hero-btn{left:207px;top:224px;width:94px;height:25px}
.dots{left:362px;top:323px;display:flex;gap:8px}
.dots i{width:10px;height:10px;border-radius:50%;background:#9ea7ae}
.mail{left:725px;top:328px;width:37px;height:37px;border-radius:50%;background:var(--blue);display:flex;align-items:center;justify-content:center}
.svc-title{left:0;top:368px;width:772px;text-align:center;font-family:"Montserrat",sans-serif;font-size:17px}
.svc{top:406px;width:220px;text-align:center}
.svc .ring{width:70px;height:70px;margin:0 auto;border:3px solid var(--blue);border-radius:50%;display:flex;align-items:center;justify-content:center}
.svc h3{margin-top:17px;font-family:"Montserrat",sans-serif;font-weight:500;font-size:13.5px;color:var(--blue)}
.svc ul{list-style:none;margin-top:11px;font-size:8.5px;color:var(--grey);line-height:17px;font-weight:300}
.svc-div{top:434px;width:1px;height:154px;background:var(--line)}
.why-bg{left:0;top:608px;width:772px;height:295px;background:linear-gradient(110deg,#f4f7fa,#fff 55%,#e4eef7)}
.why-photo{left:0;top:608px;width:380px;height:295px;background:radial-gradient(ellipse at 35% 45%,#e7c3a8,#a9836a 45%,#eef0f2 80%)}
.why h2{left:403px;top:645px;font-family:"Montserrat",sans-serif;font-weight:400;font-size:17px}
.why-copy{left:403px;top:680px;width:306px;font-size:7.8px;line-height:13px;color:var(--grey);text-align:justify;font-weight:300}
.why-list{left:404px;top:734px;list-style:none;font-size:7.8px;color:var(--grey);line-height:20px;font-weight:300}
.why-list li::before{content:"o";margin-right:15px}
.why-btn{left:405px;top:840px;width:73px;height:22px;font-size:8.5px}
.band{left:0;top:902px;width:772px;height:218px;background:linear-gradient(90deg,var(--blue-band-a),#2a78b8 50%,var(--blue-band-b))}
.band-art{left:524px;top:872px;width:188px;height:164px;background:linear-gradient(160deg,#d8e3ee,#9fb4c8);border-radius:4px}
.diamond{width:30px;height:30px;transform:rotate(45deg);border:1.5px solid rgba(255,255,255,.8);display:flex;align-items:center;justify-content:center}
.diamond svg{transform:rotate(-45deg)}
.contact-icon{left:370px;top:930px;width:32px;height:32px}
.contact-h{left:0;top:974px;width:772px;text-align:center;color:var(--white);font-size:17px;font-weight:300}
.contact-num{left:0;top:996px;width:772px;text-align:center;color:var(--white);font-size:23px;font-weight:300}
.band-rule{left:59px;top:1037px;width:650px;height:1px;background:rgba(255,255,255,.3)}
.office{top:1054px;display:flex;gap:13px;color:var(--white)}
.office .diamond{width:24px;height:24px;margin-top:5px}
.office strong{display:block;font-weight:300;font-size:13px}
.office span{font-size:9.5px;font-weight:300}
.foot-brand{left:70px;top:1138px;font-size:15px}
.copy{left:70px;top:1176px;font-size:7px;color:#444}
.foot-nav{right:63px;top:1147px;display:flex;gap:20px;font-size:8.5px}
.social{right:66px;top:1172px;display:flex;gap:13px}
.social i{width:7px;height:7px;border-radius:50%;background:#333}
.foot-rule{left:0;top:1197px;width:772px;height:3px;background:var(--blue)}
</style>
</head>
<body>
<div class="abs top-rule"></div>

<header>
  <div class="abs brand"><span class="dot"></span>Kestrel IT</div>
  <div class="abs call">
    <svg width="8" height="12" viewBox="0 0 8 12"><rect x="1" y="0.5" width="6" height="11" rx="1.2" fill="none" stroke="#1a73b8" stroke-width="1.3"/></svg>
    Call Us: <b>555-014-2200</b>
  </div>
  <nav class="abs nav">
    <span class="active">Home</span><span>Services</span><span>Why Kestrel IT</span><span>Contact</span>
    <span class="search"><svg width="9" height="9" viewBox="0 0 9 9"><circle cx="3.7" cy="3.7" r="2.6" fill="none" stroke="#fff" stroke-width="1.3"/><path d="M5.6 5.6L8 8" stroke="#fff" stroke-width="1.3"/></svg></span>
  </nav>
  <div class="abs header-rule"></div>
</header>

<section>
  <div class="abs hero"></div>
  <div class="abs hero-photo" role="img" aria-label="Support technician wearing a headset in an office"></div>
  <p class="abs hero-text">We provides commercial IT support and services to small and medium sized businesses.</p>
  <div class="abs btn hero-btn">LEARN MORE</div>
  <div class="abs dots"><i></i><i></i><i></i></div>
  <div class="abs mail"><svg width="16" height="12" viewBox="0 0 16 12"><rect x="1" y="1" width="14" height="10" rx="1" fill="none" stroke="#fff" stroke-width="1.4"/><path d="M1 1.5L8 7l7-5.5" fill="none" stroke="#fff" stroke-width="1.4"/></svg></div>
</section>

<section>
  <h2 class="abs svc-title" style="font-weight:400">Our Kestrel Services</h2>
  <div class="abs svc" style="left:55px">
    <div class="ring"><svg width="38" height="38" viewBox="0 0 38 38" fill="none" stroke="#1a73b8" stroke-width="1.3"><rect x="5" y="4" width="22" height="7"/><rect x="5" y="13" width="22" height="7"/><rect x="5" y="22" width="22" height="7"/><circle cx="28" cy="28" r="5"/><circle cx="28" cy="28" r="1.8"/></svg></div>
    <h3>Data</h3>
    <ul><li>Managed IT Services</li><li>IT Support &amp; Consulting</li><li>IT Helpdesk Services</li></ul>
  </div>
  <div class="abs svc-div" style="left:276px"></div>
  <div class="abs svc" style="left:276px">
    <div class="ring"><svg width="40" height="28" viewBox="0 0 40 28" fill="none" stroke="#1a73b8" stroke-width="1.5"><path d="M10 25h21a7 7 0 0 0 1-14 10 10 0 0 0-19-2 8 8 0 0 0-3 16z"/></svg></div>
    <h3>Cloud</h3>
    <ul><li>Officeline Suite Migrations</li><li>Nimbus Cloud Management Services</li><li>Cloud Migration Services</li></ul>
  </div>
  <div class="abs svc-div" style="left:497px"></div>
  <div class="abs svc" style="left:497px">
    <div class="ring"><svg width="34" height="36" viewBox="0 0 34 36" fill="none" stroke="#1a73b8" stroke-width="1.4"><path d="M6 20v-5a11 11 0 0 1 22 0v5"/><rect x="3" y="17" width="6" height="10" rx="2"/><rect x="25" y="17" width="6" height="10" rx="2"/><path d="M28 27c0 5-5 6-10 6"/></svg></div>
    <h3>Voice</h3>
    <ul><li>Astra PBX Consulting</li><li>Business Telephone Systems</li><li>Multiple Office Phone Systems</li></ul>
  </div>
</section>

<section class="why">
  <div class="abs why-bg"></div>
  <div class="abs why-photo" role="img" aria-label="Smiling customer support agent with a headset"></div>
  <h2 class="abs">Why Kestrel IT</h2>
  <p class="abs why-copy">Duis aute irure dolor in reprehenderit in voluptate velit esse cillum dolore eu fugiat nulla pariatur. Excepteur sint occaecat cupidatat non proident, sunt in culpa qui officia deserunt mollit anim id est laborum.</p>
  <ul class="abs why-list"><li>Network Security</li><li>Data Backup &amp; Recovery</li><li>Servers &amp;Virtualization</li><li>Remote Monitoring Services</li><li>Wireless Networking</li></ul>
  <div class="abs btn why-btn">READ MORE</div>
</section>

<section>
  <div class="abs band"></div>
  <div class="abs band-art" role="img" aria-label="Man with headset holding a contact support dialog box"></div>
  <div class="abs diamond contact-icon"><svg width="16" height="16" viewBox="0 0 16 16"><path d="M4 1.5l2.3 3-1.3 1.6a9 9 0 0 0 5 5l1.6-1.3 3 2.3-1.4 2.2C8 14 2 8 1.8 3z" fill="#fff"/></svg></div>
  <h2 class="abs contact-h">Contact Us</h2>
  <div class="abs contact-num">555-014-2200</div>
  <div class="abs band-rule"></div>
  <div class="abs office" style="left:64px"><div class="diamond"><svg width="12" height="12" viewBox="0 0 16 16"><path d="M4 1.5l2.3 3-1.3 1.6a9 9 0 0 0 5 5l1.6-1.3 3 2.3-1.4 2.2C8 14 2 8 1.8 3z" fill="#fff"/></svg></div><div><strong>Houston</strong><span>555-014-3100</span></div></div>
  <div class="abs office" style="left:197px"><div class="diamond"><svg width="12" height="12" viewBox="0 0 16 16"><path d="M4 1.5l2.3 3-1.3 1.6a9 9 0 0 0 5 5l1.6-1.3 3 2.3-1.4 2.2C8 14 2 8 1.8 3z" fill="#fff"/></svg></div><div><strong>San Antonio</strong><span>555-014-3200</span></div></div>
  <div class="abs office" style="left:329px"><div class="diamond"><svg width="12" height="12" viewBox="0 0 16 16"><path d="M4 1.5l2.3 3-1.3 1.6a9 9 0 0 0 5 5l1.6-1.3 3 2.3-1.4 2.2C8 14 2 8 1.8 3z" fill="#fff"/></svg></div><div><strong>Austin</strong><span>555-014-3300</span></div></div>
  <div class="abs office" style="left:457px"><div class="diamond"><svg width="12" height="12" viewBox="0 0 16 16"><path d="M4 1.5l2.3 3-1.3 1.6a9 9 0 0 0 5 5l1.6-1.3 3 2.3-1.4 2.2C8 14 2 8 1.8 3z" fill="#fff"/></svg></div><div><strong>Tulsa</strong><span>555-014-3400</span></div></div>
  <div class="abs office" style="left:585px"><div class="diamond"><svg width="12" height="12" viewBox="0 0 16 16"><path d="M4 1.5l2.3 3-1.3 1.6a9 9 0 0 0 5 5l1.6-1.3 3 2.3-1.4 2.2C8 14 2 8 1.8 3z" fill="#fff"/></svg></div><div><strong>Oklahoma City</strong><span>555-014-3500</span></div></div>
</section>

<footer>
  <div class="abs brand foot-brand"><span class="dot"></span>Kestrel IT</div>
  <div class="abs copy">© 2017. All rights reserved. | www.kestrelit.example</div>
  <nav class="abs foot-nav"><span>Home</span><span>Services</span><span>Why Kestrel IT</span><span>Contact</span></nav>
  <div class="abs social"><i></i><i></i><i></i><i></i></div>
  <div class="abs foot-rule"></div>
</footer>
</body>
</html>
```